Design website home page for pathology consulting company

Starting a new consulting company with anatomic pathologists focused on expert diagnosis and second opinions on difficult pathology cases. In the near future we will be incorporating next generation diagnostics for rare diseases of childhood into the business. These include discovery and testing of DNA for mutations.

The company is formed around one of the best known pathologists in the world named Marcel "Biscuit" Trowell. The name of the company is "BiscuitLab"

We had a logo design by SketchForum - it is great. I will attach file as soon as I have it (contest ending today). Our company is medical, uses microscopes, DNA, probably will focus on childhood diseases but not solely on childhood diseases. we're not particularly conservative, but the customers we want to appeal to include older practicing pathologists as well as patients (sometimes parents) looking for second opinions.

Think a group of expert doctors diagnosing disease through the microscope and through DNA technology, ages ranging from 35-75 all trained by the best pathologist in the world - "Biscuit"

We receive glass slides from diseases from patients all over the world from docs who need an expert to tell them what is the diagnosis. So "path to the diagnosis" is also part of the company marketing message.

We want the website design to describe our company but be very simple to find what one is looking for as we will use it as the launch page to:
1) order services
2) check results/reports
3) set up new account
4) speak with one of the pathologists
5) see our test menu
6) access our educational material/webinars
Updates

Update - looking for home page design and then finalists will ask for second page design to keep with theme - ok?

Reason: realized this project isn't web design but web home page design - thanks

Reason: Holidays for some in next two weeks

Reason: Hot discussion among collaborators for a few of the submissions. Will provide detail individually this weekend. Thanks so much for all the submissions!

Target Market(s)

Referring pathologists, physicians who want second opinions on pathology disease diagnosis, patients who have had biopsies (either patients themselves or parents of patients), generally high education level

Industry/Entity Type

Marketing

Requirements
Must have
• BiscuitLab
Next Generation Pathology Consultants

```html
<!DOCTYPE html>
<html lang="en">
<head>
<meta charset="utf-8">
<title>BiscuitLab – Next Generation Pathology Consultants</title>
<link href="https://fonts.googleapis.com/css2?family=Open+Sans:ital,wght@0,300;0,400;0,600;0,700;1,400&display=swap" rel="stylesheet">
<style>
:root{
  --blue:#0d58a8;
  --blue-dark:#0a3f85;
  --nav-top:#2a8ee0;
  --nav-bottom:#0c5fb8;
  --footer:#2c68ae;
  --footer-bar:#1a4b8a;
  --ink:#222;
  --grey-text:#7a7a7a;
  --band:#f4f4f4;
  --section-grey:#ebebeb;
  --ring:#b9bcc0;
  --button:#2f86e6;
  --button-light:#5aaadf;
}
*{margin:0;padding:0;box-sizing:border-box}
html,body{width:824px;height:1200px;overflow:hidden;background:#fff}
body{font-family:"Open Sans",sans-serif;color:var(--ink);position:relative}
.abs{position:absolute}

/* header */
.header{left:0;top:0;width:824px;height:75px;background:#e9e9e9}
.brand{left:84px;top:6px;display:flex;align-items:center;gap:8px}
.brand-dot{width:64px;height:64px;border-radius:50%;background:#c9ccd0}
.brand-name{font-size:24px;font-weight:600;color:var(--blue);letter-spacing:.5px;line-height:1}
.brand-tag{font-size:8px;color:#777;margin-top:3px}
.account{right:97px;top:33px;font-size:8.5px;font-weight:700;color:#111}
.account span{margin:0 8px}
.ribbon{left:733px;top:0}

/* nav */
.nav{left:0;top:75px;width:824px;height:50px;background:linear-gradient(var(--nav-top),var(--nav-bottom))}
.nav-item{top:0;height:50px;line-height:50px;font-size:9px;font-weight:700;color:#fff}
.nav-active{left:76px;width:52px;background:#3a3a3a;text-align:center}

/* hero */
.hero{left:0;top:125px;width:824px;height:375px;background:linear-gradient(100deg,#d9dcdf 0%,#a9adb2 35%,#5d6269 60%,#3e4349 100%)}
.hero-title{left:446px;top:162px;font-size:27px;font-weight:600;color:#fff}
.hero-text{left:448px;top:202px;width:290px;font-size:8.5px;line-height:13px;color:#fff}
.hero-btn{left:449px;top:242px;width:98px;height:23px;background:var(--button);border:1px solid #9cc8f5;color:#fff;font-size:12px;font-weight:600;text-align:center;line-height:21px}
.arrow{top:292px}

/* order band */
.band{left:0;top:500px;width:824px;height:72px;background:var(--band)}
.band-text{left:92px;top:524px;font-size:17.5px;font-weight:300;color:#777}
.band-btn{left:596px;top:519px;width:136px;height:33px;background:var(--button);border:1px solid #1c5fb0;color:#fff;font-size:8.5px;font-weight:700;text-align:center;line-height:31px}

/* features */
.feature{top:590px;width:180px;text-align:center}
.feature-ring{width:90px;height:90px;border-radius:50%;background:var(--ring);margin:0 auto;display:flex;align-items:center;justify-content:center}
.feature-core{width:80px;height:80px;border-radius:50%;background:var(--blue);display:flex;align-items:center;justify-content:center}
.feature-title{font-size:13.5px;font-weight:600;color:var(--blue);margin-top:12px}
.feature-text{font-size:8.5px;line-height:13px;color:var(--grey-text);margin-top:6px}

/* microscope section */
.section{left:0;top:766px;width:824px;height:229px;background:var(--section-grey)}
.photo-frame{left:76px;top:797px;width:240px;height:168px;background:#fff;padding:5px}
.photo-fill{width:100%;height:100%;background:linear-gradient(120deg,#1f4fae,#5a7ec4 45%,#c9b8a8 65%,#3a3f4a)}
.article-title{left:326px;top:794px;font-size:14px;font-weight:600;color:var(--blue)}
.article-text{left:327px;top:820px;width:212px;font-size:8px;line-height:15.2px;color:var(--grey-text)}
.sidebar{left:584px;top:797px;width:176px;height:172px;background:#fafafa;text-align:center}
.sidebar-title{margin-top:8px;font-size:12px;line-height:13px;font-weight:700;color:var(--blue)}
.sidebar-photo{width:92px;height:72px;margin:3px auto 0;background:linear-gradient(#d8dde3,#e9d4c2 50%,#f0f2f4)}
.sidebar-text{width:100px;margin:2px 0 0 41px;text-align:left;font-size:7px;line-height:13px;color:#222}
.call-btn{left:630px;top:948px;width:80px;height:16px;background:var(--blue-dark);color:#fff;font-size:8.5px;text-align:center;line-height:16px}

/* footer */
.footer{left:0;top:995px;width:824px;height:177px;background:var(--footer);color:#fff}
.f-head{top:1006px;font-size:10px;font-weight:700;color:#fff}
.f-text{left:84px;top:1030px;width:180px;font-size:8.5px;line-height:13px;color:#fff}
.f-btn{left:84px;top:1116px;width:86px;height:16px;background:var(--button-light);color:#123;font-size:8.5px;text-align:center;line-height:16px}
.menu{left:297px;top:1032px;list-style:none;font-size:8.5px;color:#fff}
.menu li{height:25.6px}
.menu li::before{content:"›";margin-right:6px;font-size:8px}
.social{left:418px;top:1032px;display:flex;gap:8px}
.social span{width:23px;height:23px;background:#3c4a5e;display:block}
.email{left:418px;top:1090px;width:126px;height:18px;background:var(--blue-dark);font-size:8.5px;font-weight:600;padding-left:7px;line-height:18px;color:#fff}
.enter{left:487px;top:1118px;width:56px;height:16px;background:var(--button-light);color:#123;font-size:8.5px;font-weight:600;text-align:center;line-height:16px}
.loc{left:607px;font-size:8.5px;line-height:10px;font-weight:600;color:#fff;display:flex;gap:5px}
.wait-small{left:616px;top:1113px;font-size:10.5px;color:#fff}
.wait-big{left:614px;top:1125px;font-size:17px;color:#fff}
.wait-dial{left:700px;top:1106px;width:52px;height:52px;border-radius:50%;background:radial-gradient(#d8d8d8,#a9a9a9);color:#fff;font-style:italic;font-size:16px;line-height:15px;text-align:center;padding-top:11px}
.bar{left:0;top:1172px;width:824px;height:28px;background:var(--footer-bar);color:#fff;font-size:8px;font-weight:600}
.copy{left:84px;top:9px}
.legal{right:73px;top:9px}
.legal span{margin:0 9px}
</style>
</head>
<body>

<header class="abs header">
  <div class="abs brand">
    <div class="brand-dot"></div>
    <div>
      <div class="brand-name">BiscuitLab</div>
      <div class="brand-tag">Next Generation Pathology Consultants</div>
    </div>
  </div>
  <div class="abs account">REGISTER<span>|</span>LOGIN</div>
  <svg class="abs ribbon" width="27" height="62" viewBox="0 0 27 62">
    <path d="M0 0H27V62L13.5 51L0 62Z" fill="#2b86d6"/>
    <circle cx="13.5" cy="25" r="7" fill="#fff"/>
    <path d="M13.5 21v8M9.5 25h8" stroke="#2b86d6" stroke-width="2"/>
  </svg>
</header>

<nav class="abs nav">
  <div class="abs nav-item nav-active">HOME</div>
  <div class="abs nav-item" style="left:152px">PHYSICIANS</div>
  <div class="abs nav-item" style="left:229px">SPECIALITIES</div>
  <div class="abs nav-item" style="left:310px">INFO</div>
  <div class="abs nav-item" style="left:364px">LOCATIONS</div>
  <div class="abs nav-item" style="left:440px">CONTACT</div>
</nav>

<section class="abs hero" role="img" aria-label="Pathologist looking through a microscope beside a laptop showing cell imagery"></section>
<h1 class="abs hero-title">Path To The Diagnosis</h1>
<p class="abs hero-text">Lorem ipsum dolor sit amet, consecteturadipiscing elit. Niihunclorem est eleifend in nunc.</p>
<div class="abs hero-btn">READ MORE</div>
<svg class="abs arrow" style="left:76px" width="16" height="32" viewBox="0 0 16 32"><path d="M13 2L4 16L13 30" fill="none" stroke="#1a6fc4" stroke-width="4"/></svg>
<svg class="abs arrow" style="left:742px" width="16" height="32" viewBox="0 0 16 32"><path d="M3 2L12 16L3 30" fill="none" stroke="#1a6fc4" stroke-width="4"/></svg>

<section class="abs band"></section>
<p class="abs band-text">Order Services Where You Want In Just 10 Minutes !</p>
<div class="abs band-btn">CHECK RESULT/ REPORT</div>

<div class="abs feature" style="left:65px">
  <div class="feature-ring"><div class="feature-core">
    <svg width="36" height="40" viewBox="0 0 36 40"><circle cx="16" cy="7" r="6" fill="#fff"/><path d="M8 16h14c6 0 10 5 10 11s-5 11-12 11H12c-4 0-6-3-4-6l3-4c-3-2-5-8-3-12Z" fill="#fff"/><circle cx="21" cy="27" r="5" fill="#0d58a8"/></svg>
  </div></div>
  <div class="feature-title">Childhood Diseases</div>
  <p class="feature-text">Lorem ipsum dolor sit amet, consectetur adipiscing elit. Niihunclorem est, eleifend elefend in nunc.</p>
</div>
<div class="abs feature" style="left:332px">
  <div class="feature-ring"><div class="feature-core">
    <svg width="34" height="34" viewBox="0 0 34 34"><circle cx="17" cy="10" r="8" fill="#fff"/><path d="M2 32c0-9 6-13 15-13s15 4 15 13Z" fill="#fff"/></svg>
  </div></div>
  <div class="feature-title">Second opinion</div>
  <p class="feature-text">Lorem ipsum dolor sit amet, consectetur adipiscing elit. Niihunclorem est, eleifend elefend in nunc.</p>
</div>
<div class="abs feature" style="left:590px">
  <div class="feature-ring"><div class="feature-core">
    <svg width="20" height="44" viewBox="0 0 20 44"><path d="M3 2C3 12 17 12 17 22S3 32 3 42M17 2C17 12 3 12 3 22S17 32 17 42" fill="none" stroke="#fff" stroke-width="3"/><path d="M6 7h8M6 17h8M6 27h8M6 37h8" stroke="#fff" stroke-width="2"/></svg>
  </div></div>
  <div class="feature-title">DNA Technology</div>
  <p class="feature-text">Lorem ipsum dolor sit amet, consectetur adipiscing elit. Niihunclorem est, eleifend elefend in nunc.</p>
</div>

<section class="abs section"></section>
<div class="abs photo-frame"><div class="photo-fill" role="img" aria-label="Pathologist working at a laboratory microscope"></div></div>
<h2 class="abs article-title">Dignosis Using Microscopes</h2>
<p class="abs article-text">Lorem ipsum dolor sit amet, consecteturelit. Niihunclo-rem est,eleifend velcursrtus aelefend in nunc. Nulla agcigisi.moirbi sce ierisque serm vitea massa feugiatut varipusmhurisorganarie.sed prelium felts eget adminut varipus mhurisorganarie.<br>Lorem ipsum dolor sit amet, consecteturelit. Niihunclo-rem est,eleifend velcursrtus aelefend in nunc. Nulla agcigisi.moirbi sce ierisque serm vitea massa feugiatut varipusmhurisorganarie.</p>
<aside class="abs sidebar">
  <div class="sidebar-title">Speak With One<br>Of The pathologist</div>
  <div class="sidebar-photo" role="img" aria-label="Smiling pathologist beside a microscope"></div>
  <p class="sidebar-text">Lorem ipsum dolor sit amet, adipiscing elit. Niihunclorem elefend in nunc.</p>
</aside>
<div class="abs call-btn">CALL NOW</div>

<footer class="abs footer"></footer>
<div class="abs f-head" style="left:84px">Access Our Educational Materials</div>
<p class="abs f-text">Lorem ipsum dolor sit amet, adipiscing elit. Niihunclorem elefend in nunc.<br>Lorem ipsum dolor sit amet, adipiscing elit. Niihunclorem elefend in nunc.<br>Lorem ipsum dolor sit amet, adipiscing elit. Niihunclorem elefend in nunc.</p>
<div class="abs f-btn">MORE DETAIL</div>

<div class="abs f-head" style="left:297px">Test Menu</div>
<ul class="abs menu"><li>HOME</li><li>PHYSICIANS</li><li>SPECIALITIES</li><li>INFO</li></ul>

<div class="abs f-head" style="left:419px">Contact</div>
<div class="abs social"><span></span><span></span><span></span><span></span></div>
<div class="abs f-head" style="left:418px;top:1068px">New account</div>
<div class="abs email">Enter your Email :</div>
<div class="abs enter">Enter</div>

<div class="abs f-head" style="left:607px">Locations</div>
<div class="abs loc" style="top:1032px">
  <svg width="7" height="10" viewBox="0 0 7 10"><path d="M3.5 0A3.5 3.5 0 0 0 0 3.5C0 6 3.5 10 3.5 10S7 6 7 3.5A3.5 3.5 0 0 0 3.5 0Z" fill="#fff"/><circle cx="3.5" cy="3.5" r="1.3" fill="#2c68ae"/></svg>
  <div>alder lane ,name .city ,country<br>zip code : 204518</div>
</div>
<div class="abs loc" style="top:1066px">
  <svg width="7" height="10" viewBox="0 0 7 10"><path d="M3.5 0A3.5 3.5 0 0 0 0 3.5C0 6 3.5 10 3.5 10S7 6 7 3.5A3.5 3.5 0 0 0 3.5 0Z" fill="#fff"/><circle cx="3.5" cy="3.5" r="1.3" fill="#2c68ae"/></svg>
  <div>alder lane ,name .city ,country<br>zip code : 204518</div>
</div>
<div class="abs wait-small">Average</div>
<div class="abs wait-big">wait time</div>
<div class="abs wait-dial">9<br>min</div>

<div class="abs bar">
  <div class="abs copy">COPYRIGHT © 2013. BISCUITLAB ALL RIGHTS RESERVED.</div>
  <div class="abs legal">SITEMAP<span>|</span>PRIVACY POLICY</div>
</div>

</body>
</html>
```